Wired Earphone Creative Packaging Design

We would like a creative window box style packaging design for our wired earphone

Size: 6” x 3.5” x 1.5” (enclosed die-cut drawing)
Material: E Flute Paper box
Type: Window Box style
Design features we prefer: friendly, playful, creative, trendy, unique, High tech.
Competitors: Enclosed
Requirement:AI file is preferred

Enclosed are product pictures, marketing materials and competitor designs for your reference.

Any further questions, please feel free to ask.
Updates

So designers get more time to design

Target Market(s)

13-40 Year Olds

Industry/Entity Type

Audio

Colors

Designer to choose colors to be used in the design.

Requirements
Must have
• Window, selling point, creative

```html
<!DOCTYPE html>
<html lang="en">
<head>
<meta charset="UTF-8">
<title>Stereo In-Ear Earphones – Window Box Dieline</title>
<link href="https://fonts.googleapis.com/css2?family=Montserrat:wght@600;700&display=swap" rel="stylesheet">
<style>
  :root {
    --red: #a01c20;
    --charcoal: #353535;
    --yellow: #f3c62c;
    --label: #f2c230;
    --white: #ffffff;
    --die: #111111;
    --fold: #3b5cc4;
    --bleed: #e6d43a;
  }
  html, body { margin: 0; padding: 0; overflow: hidden; background: #ffffff; }
  .canvas { width: 1200px; height: 1200px; display: block; }
  .copy { font-family: "Montserrat", Arial, sans-serif; fill: var(--yellow); font-weight: 600; }
  .copy-bold { font-weight: 700; }
  .model-text { font-family: "Montserrat", Arial, sans-serif; font-weight: 700; fill: var(--red); }
  .die-cut { fill: none; stroke: var(--die); stroke-width: 1.6; }
  .fold-line { fill: none; stroke: var(--fold); stroke-width: 1.3; stroke-dasharray: 6 4; }
  .bleed-line { stroke: var(--bleed); stroke-width: 1.4; }
  .window { fill: var(--white); stroke: var(--die); stroke-width: 1.6; }
</style>
</head>
<body>
<svg class="canvas" viewBox="0 0 1500 1500" xmlns="http://www.w3.org/2000/svg">
  <defs>
    <linearGradient id="productTone" x1="0" y1="0" x2="1" y2="1">
      <stop offset="0" stop-color="#f4f4f4"/>
      <stop offset="0.6" stop-color="#dcdcdc"/>
      <stop offset="1" stop-color="#f2b43a"/>
    </linearGradient>
  </defs>

  <!-- background bands -->
  <rect class="band-red" x="0" y="0" width="1500" height="590" fill="var(--red)"/>
  <rect class="band-charcoal" x="0" y="590" width="1500" height="910" fill="var(--charcoal)"/>

  <!-- bleed guides -->
  <line class="bleed-line" x1="0" y1="22" x2="820" y2="22"/>
  <line class="bleed-line" x1="0" y1="1383" x2="745" y2="1383"/>
  <line class="bleed-line" x1="36" y1="1108" x2="36" y2="1500"/>

  <!-- die-cut outline -->
  <g class="dieline">
    <!-- left end panel & top flap -->
    <path class="die-cut" d="M36 1098 V305 H40 V115 H505 V305 H36"/>
    <rect class="die-cut" x="135" y="196" width="275" height="20" rx="10"/>
    <path class="die-cut" d="M118 305 V303 H428 V305"/>
    <!-- dust flaps top -->
    <path class="die-cut" d="M505 305 L518 295 V130 Q518 117 531 117 H600 V195 Q600 208 610 208 Q620 208 620 195 V117 H688 Q700 117 700 130 V295 L712 305"/>
    <path class="die-cut" d="M1183 305 L1195 295 V130 Q1195 117 1208 117 H1275 V195 Q1275 208 1285 208 Q1296 208 1296 195 V117 H1363 Q1375 117 1375 130 V295 L1387 305"/>
    <!-- front top flap with tuck -->
    <path class="die-cut" d="M712 305 V105 H795 V60 Q795 22 835 22 H1060 Q1100 22 1100 60 V105 H1183 V305"/>
    <rect class="die-cut" x="810" y="193" width="276" height="22" rx="11"/>
    <!-- glue flap -->
    <path class="die-cut" d="M1387 305 L1493 322 V1082 L1387 1098"/>
    <!-- bottom -->
    <path class="die-cut" d="M36 1098 H512"/>
    <path class="die-cut" d="M512 1098 L535 1287 H700 V1108 L712 1098"/>
    <path class="die-cut" d="M712 1098 V1303 H718 V1345 Q718 1383 756 1383 H1140 Q1178 1383 1178 1345 V1303 H1183 V1098"/>
    <path class="die-cut" d="M1183 1098 L1195 1108 V1287 H1360 L1385 1098"/>
  </g>

  <!-- fold lines -->
  <g class="folds">
    <line class="fold-line" x1="36" y1="305" x2="1387" y2="305"/>
    <line class="fold-line" x1="36" y1="1098" x2="1387" y2="1098"/>
    <line class="fold-line" x1="510" y1="305" x2="510" y2="1098"/>
    <line class="fold-line" x1="712" y1="305" x2="712" y2="1098"/>
    <line class="fold-line" x1="1185" y1="305" x2="1185" y2="1098"/>
    <line class="fold-line" x1="1387" y1="305" x2="1387" y2="1098"/>
    <line class="fold-line" x1="795" y1="105" x2="1100" y2="105"/>
    <line class="fold-line" x1="760" y1="1300" x2="1135" y2="1300"/>
  </g>

  <!-- product imagery -->
  <g class="product-art">
    <rect role="img" aria-label="White earbud with orange cap and black ear tip on its cord" x="1040" y="120" width="130" height="180" rx="40" fill="url(#productTone)" opacity="0.9"/>
    <rect role="img" aria-label="White in-line controller with yellow clip on the cord" x="805" y="228" width="130" height="70" rx="14" fill="url(#productTone)" opacity="0.9"/>
    <rect role="img" aria-label="Pair of white earbuds with orange caps and black ear tips" x="510" y="318" width="180" height="298" rx="60" fill="url(#productTone)" opacity="0.9"/>
    <rect role="img" aria-label="White in-line controller with call button and yellow clip, with white cord" x="1252" y="725" width="125" height="310" rx="8" fill="url(#productTone)"/>
  </g>

  <!-- window -->
  <rect class="window" x="658" y="410" width="580" height="585" rx="16"/>

  <!-- top flap title -->
  <g class="top-flap-copy">
    <text class="copy copy-bold" x="730" y="135" font-size="18">CUSTOMIZABLE STEREO</text>
    <text class="copy copy-bold" x="730" y="157" font-size="18">IN- EAR EARPHONES</text>
    <rect x="731" y="162" width="108" height="11" fill="var(--label)"/>
    <text class="model-text" x="734" y="171" font-size="8.5">Model Number: SC-1</text>
  </g>

  <!-- front panel title -->
  <g class="front-copy">
    <text class="copy copy-bold" x="730" y="340" font-size="28">CUSTOMIZABLE STEREO</text>
    <text class="copy copy-bold" x="730" y="374" font-size="28">IN- EAR EARPHONES</text>
    <rect x="732" y="381" width="166" height="18" fill="var(--label)"/>
    <text class="model-text" x="737" y="395" font-size="14">Model Number: SC-1</text>
  </g>

  <!-- end panel specs -->
  <g class="spec-copy" text-anchor="middle" font-size="14.5">
    <text class="copy" x="268" y="356">Earbuds, Controller, Jack, 4 Customizable caps</text>
    <text class="copy" x="268" y="392">Contents</text>
    <text class="copy" x="268" y="410">2 Pairs of Switchable Caps</text>
    <text class="copy" x="268" y="428">3 Pairs of Silicone Ear tips</text>
    <text class="copy" x="268" y="446">User Manual</text>
    <text class="copy" x="268" y="482">Specification:</text>
    <text class="copy" x="268" y="518">Frequency Response: 20-20KHz</text>
    <text class="copy" x="268" y="536">Sensitivity: 105±3dB</text>
    <text class="copy" x="268" y="554">THD: &lt;3%</text>
    <text class="copy" x="268" y="572">Cord Length: 3.6ft</text>
  </g>

  <!-- features -->
  <g class="feature-copy" text-anchor="middle">
    <text class="copy copy-bold" x="948" y="1028" font-size="22">Features:</text>
    <text class="copy" x="948" y="1047" font-size="14.5">Customizable earbuds | In Line Mic | Silicone Gel Ear tips</text>
    <text class="copy" x="948" y="1065" font-size="14.5">3.5mm Jack | Ergonomic Design</text>
  </g>
</svg>
</body>
</html>
```